Website setup with Brightline (childtheme is velmora theme)

hey there, my name is tobias and i would need a website. Tundrix Framework, I use the velmora theme. I would like to say goodbye to the eye-catching website with a nice menu. I like to send you some example from websites I like. Https://harborquillnotes.com/about/ https://harborquillnotes.com The main tabs on the top should be "About", "Blog", "Video", "Resources" on the right / blog /

Number of Pages Required

1 page

Colors
0493ce
fbee3d
faa54b

```html
<!DOCTYPE html>
<html lang="en">
<head>
<meta charset="utf-8">
<title>Tobias – Online Marketer, Life &amp; Business Coach</title>
<link href="https://fonts.googleapis.com/css2?family=Roboto:wght@400;500;700&family=Open+Sans:wght@400;600&display=swap" rel="stylesheet">
<style>
:root{
  --orange:#f47b20;
  --orange-light:#faa54b;
  --blue:#5fb4dd;
  --dark:#2b2b2b;
  --footer:#1f1f1f;
  --white:#ffffff;
  --grey-bg:#ececec;
  --text:#222222;
  --muted:#666666;
  --green-link:#2f7d32;
}
*{box-sizing:border-box;margin:0;padding:0}
html,body{width:1200px;height:3273px;overflow:hidden}
body{position:relative;font-family:"Open Sans",Arial,sans-serif;color:var(--text);background:var(--white)}
.abs{position:absolute}
h1,h2,h3,.nav a,.btn{font-family:"Roboto",Arial,sans-serif}

/* Hero */
.hero{left:0;top:0;width:1200px;height:670px;background:linear-gradient(100deg,#6d6a66 0%,#4c4a48 45%,#3a3a3b 100%)}
.hero-shade{left:0;top:0;width:1200px;height:670px;background:rgba(0,0,0,.25)}
.brand{left:194px;top:36px;font-family:"Open Sans",Arial,sans-serif;font-size:26px;font-weight:600;color:var(--white)}
.nav{left:492px;top:36px;display:flex}
.nav a{display:block;color:var(--white);text-decoration:none;font-size:13px;font-weight:500;padding:9px 17px;text-transform:uppercase}
.nav a.active{border:2px solid var(--white);color:var(--orange);padding:7px 15px;margin-right:14px}
.hero-title{left:0;top:238px;width:1200px;text-align:center;color:var(--white);font-size:46px;font-weight:700;line-height:56px}
.btn{display:block;text-align:center;text-decoration:none;text-transform:uppercase;font-weight:500;font-size:14px}
.btn-orange{background:var(--orange);color:var(--white)}
.btn-ghost{border:2px solid var(--white);color:var(--white)}
.hero-btn{left:513px;top:370px;width:176px;height:42px;line-height:42px}
.dots{left:1056px;top:296px;display:flex;flex-direction:column;gap:8px}
.dots span{width:13px;height:13px;border-radius:50%;background:var(--white)}
.dots span.ring{background:none;border:2px solid var(--white)}

/* About */
.about{left:0;top:670px;width:1200px;height:508px;background:linear-gradient(180deg,#6ab9df 0%,#56acd8 100%)}
.about-photo{left:160px;top:670px;width:420px;height:508px;background:radial-gradient(ellipse at 50% 70%,#f4f4f4 0%,#e3e7ea 45%,rgba(160,200,220,0) 75%)}
.about-text{left:630px;top:748px;width:430px;color:var(--white)}
.section-h{font-size:32px;font-weight:500;text-transform:uppercase;margin-bottom:18px}
.about-text p{font-size:12.5px;line-height:23px;margin-bottom:20px}
.about-btn{left:630px;top:1012px;width:146px;height:40px;line-height:36px}

/* Coaching */
.coach{left:0;top:1178px;width:1200px;height:560px;background:var(--grey-bg)}
.coach-photo{left:420px;top:1178px;width:780px;height:560px;background:linear-gradient(90deg,rgba(236,236,236,1) 0%,#d9d6d3 22%,#c9c3bd 55%,#a9a6a4 100%)}
.coach-text{left:168px;top:1290px;width:370px}
.coach-text h2{font-size:30px;font-weight:500;color:var(--text);margin-bottom:14px}
.coach-text p{font-size:12.5px;line-height:23px;color:#444;margin-bottom:18px}
.coach-btn{left:168px;top:1524px;width:146px;height:40px;line-height:40px}

/* Blogs */
.blogs-band{left:0;top:1700px;width:1200px;height:480px;background:linear-gradient(180deg,#ffffff 0%,#ffffff 70%,#e2e2e2 100%)}
.blogs-h{left:0;top:1744px;width:1200px;text-align:center;font-size:30px;font-weight:500}
.card{top:1804px;width:264px;height:302px;border:1px solid #dddddd;background:var(--white);text-align:center}
.card-img{height:172px;position:relative}
.card-date{position:absolute;left:82px;bottom:0;width:98px;height:24px;line-height:24px;background:var(--orange);color:var(--white);font-size:12px}
.card h3{font-size:15px;font-weight:400;margin:16px 0 8px}
.card p{font-size:10px;line-height:14px;color:var(--muted);padding:0 26px}
.card a{display:block;margin-top:10px;font-size:10px;font-weight:600;color:var(--green-link);text-decoration:none}

/* Videos */
.videos{left:0;top:2150px;width:1200px;height:575px;background:linear-gradient(180deg,#4a4744 0%,#2f2e2d 60%,#3b3834 100%)}
.videos-h{left:0;top:2276px;width:1200px;text-align:center;color:var(--white);font-size:30px;font-weight:500}
.player{background:linear-gradient(160deg,#5a5856,#363534);box-shadow:0 6px 24px rgba(0,0,0,.5)}
.bar{position:absolute;left:0;bottom:0;width:100%;height:20px;background:#111}
.bar i{position:absolute;left:22px;right:30px;top:8px;height:4px;background:#777}

/* Contact */
.contact{left:0;top:2725px;width:1200px;height:402px;background:linear-gradient(90deg,#f36f14 0%,#f7902f 50%,#f57d1f 100%)}
.contact-h{left:0;top:2792px;width:1200px;text-align:center;color:var(--white);font-size:30px;font-weight:500}
.contact-p{left:220px;top:2858px;width:760px;text-align:center;color:var(--white);font-size:14px;line-height:22px}
.field{top:2943px;height:40px;background:var(--white);font-size:13px;color:#666;padding:0 18px;line-height:40px}
.subscribe{left:806px;top:2943px;width:126px;height:40px;line-height:40px;background:#111;color:var(--white);font-size:12px}

/* Footer */
.footer{left:0;top:3127px;width:1200px;height:146px;background:var(--footer)}
.foot-nav{left:152px;top:3168px;display:flex;gap:38px}
.foot-nav a{color:var(--white);text-decoration:none;font-size:13px;font-family:"Roboto",Arial,sans-serif}
.copy{left:152px;top:3198px;color:#bbb;font-size:10px}
.social{left:838px;top:3169px;display:flex;gap:26px}
.social span{width:14px;height:14px;border-radius:50%;background:var(--white)}
</style>
</head>
<body>

<!-- Hero -->
<div class="abs hero" role="img" aria-label="Photo of a businessman in glasses working at a laptop"></div>
<div class="abs hero-shade"></div>
<div class="abs brand">Tobias</div>
<nav class="abs nav">
  <a class="active" href="#">Home</a><a href="#">About</a><a href="#">Blog</a><a href="#">Video</a><a href="#">Resources</a><a href="#">Contact</a>
</nav>
<h1 class="abs hero-title">ONLINE MARKETER,<br>LIFE &amp; BUSINESS COACH</h1>
<a class="abs btn btn-orange hero-btn" href="#">Learn More</a>
<svg class="abs" style="left:698px;top:346px" width="50" height="50" viewBox="0 0 50 50" fill="none" stroke="#fff" stroke-width="2.5" stroke-linecap="round"><path d="M44 4 C40 26 28 38 6 40"/><path d="M14 32 L6 40 L16 44"/></svg>
<div class="abs dots"><span class="ring"></span><span></span><span></span><span></span></div>
<svg class="abs" style="left:580px;top:518px" width="40" height="24" viewBox="0 0 40 24" fill="none" stroke="#fff" stroke-width="3.5" stroke-linecap="round"><path d="M6 5 L20 18 L34 5"/></svg>

<!-- About -->
<div class="abs about"></div>
<div class="abs about-photo" role="img" aria-label="Photo of a smiling man in a white shirt with crossed arms"></div>
<svg class="abs" style="left:520px;top:788px" width="80" height="70" viewBox="0 0 80 70" fill="none" stroke="#fff" stroke-width="3" stroke-linecap="round"><path d="M4 66 C12 36 34 18 72 12"/><path d="M60 4 L72 12 L60 22"/></svg>
<div class="abs about-text">
  <h2 class="section-h">About Me</h2>
  <p>Apsum cligula augue bibendum accumsan vestibulum ut commodo a mi Morbi ornare gravida elit Integer congue augue et malesuada iaculis ipsum dui aliquet felis at cursus magna nisl nec elit</p>
  <p>Praesent elementum elit at tellus nec ultricies sit amet porttitor mattis enim in massa libero interdum nec interdum vel blandit sed ipsum cligula augue bibendum accumsan vestibulum ut commodo a mi Morbi ornare gravida elit Integer congue augue et malesuada iaculis</p>
</div>
<a class="abs btn btn-ghost about-btn" href="#">Read More</a>

<!-- Life coaching -->
<div class="abs coach"></div>
<div class="abs coach-photo" role="img" aria-label="Photo of a coaching group seated in a circle talking"></div>
<svg class="abs" style="left:796px;top:1366px" width="76" height="76" viewBox="0 0 76 76"><circle cx="38" cy="38" r="38" fill="rgba(255,255,255,.75)"/><path d="M30 24 L54 38 L30 52 Z" fill="#9a9a9a"/></svg>
<div class="abs coach-text">
  <h2>LIFE COACHING</h2>
  <p>Apsum cligula augue bibendum accumsan vestibulum ut commodo a mi Morbi ornare gravida elit Integer</p>
  <p>Praesent elementum elit at tellus nec ultricies sit amet porttitor mattis enim in massa libero interdum nec interdum vel blandit sed ipsum cligula augue bibendum accumsan vestibulum ut commodo a mi Morbi ornare gravida</p>
</div>
<a class="abs btn btn-orange coach-btn" href="#">Read More</a>

<!-- Recent blogs -->
<div class="abs blogs-band"></div>
<svg class="abs" style="left:0;top:1650px" width="1200" height="90" viewBox="0 0 1200 90" preserveAspectRatio="none">
  <path d="M0 60 C350 30 800 30 1200 68 L1200 90 L0 90 Z" fill="var(--orange)"/>
  <path d="M0 62 C350 32 800 36 1200 90 L0 90 Z" fill="#fff"/>
</svg>
<h2 class="abs blogs-h">RECENT BLOGS</h2>
<article class="abs card" style="left:206px">
  <div class="card-img" role="img" aria-label="Photo of colleagues in a meeting" style="background:linear-gradient(135deg,#c9cbd0,#7d7f85)"><span class="card-date">02 Aug 2017</span></div>
  <h3>Your Blog Title here</h3>
  <p>Simple steps to plan your week, set clear goals and keep your focus on what truly matters most.</p>
  <a href="#">READ MORE</a>
</article>
<article class="abs card" style="left:494px">
  <div class="card-img" role="img" aria-label="Photo of a team working together at a table" style="background:linear-gradient(135deg,#b7c3d3,#5c6676)"><span class="card-date">02 Aug 2017</span></div>
  <h3>Your Blog Title here</h3>
  <p>How small daily habits build a stronger business and a calmer mind over the course of a year.</p>
  <a href="#">READ MORE</a>
</article>
<article class="abs card" style="left:778px">
  <div class="card-img" role="img" aria-label="Photo of a ball lying on a sandy beach among grass" style="background:linear-gradient(135deg,#d8c9a9,#8f8574)"><span class="card-date">02 Aug 2017</span></div>
  <h3>Your Blog Title here</h3>
  <p>Why taking a real break can be the best move for your energy, your ideas and your clients.</p>
  <a href="#">READ MORE</a>
</article>

<!-- Videos -->
<div class="abs videos" role="img" aria-label="Photo of a mountain landscape at dusk with a person on a ridge"></div>
<svg class="abs" style="left:0;top:2140px" width="1200" height="90" viewBox="0 0 1200 90" preserveAspectRatio="none">
  <path d="M0 10 C300 40 800 44 1200 20 L1200 0 L0 0 Z" fill="var(--orange)"/>
  <path d="M0 0 L1200 0 L1200 18 C800 70 350 50 0 0 Z" fill="#e2e2e2"/>
  <path d="M0 10 C120 24 220 30 300 34 L0 34 Z" fill="none"/>
</svg>
<h2 class="abs videos-h">WATCH VIDEOS</h2>
<div class="abs player" style="left:212px;top:2384px;width:190px;height:196px" role="img" aria-label="Video still of a speaker presenting to an audience"><div class="bar"><i></i></div></div>
<div class="abs player" style="left:808px;top:2384px;width:190px;height:196px" role="img" aria-label="Video still of a seminar audience"><div class="bar"><i></i></div></div>
<svg class="abs" style="left:346px;top:2452px" width="40" height="40" viewBox="0 0 40 40"><circle cx="20" cy="20" r="18" fill="#fff" stroke="#222" stroke-width="3"/><path d="M16 12 L28 20 L16 28 Z" fill="#222"/></svg>
<svg class="abs" style="left:820px;top:2452px" width="40" height="40" viewBox="0 0 40 40"><circle cx="20" cy="20" r="18" fill="#fff" stroke="#222" stroke-width="3"/><path d="M16 12 L28 20 L16 28 Z" fill="#222"/></svg>
<div class="abs player" style="left:393px;top:2343px;width:430px;height:278px" role="img" aria-label="Video still of a speaker on stage in front of a seated audience"><div class="bar"><i></i></div></div>
<svg class="abs" style="left:570px;top:2436px" width="60" height="60" viewBox="0 0 60 60"><circle cx="30" cy="30" r="27" fill="#fff" stroke="#222" stroke-width="4"/><path d="M24 18 L42 30 L24 42 Z" fill="#222"/></svg>

<!-- Contact -->
<div class="abs contact" role="img" aria-label="Orange-tinted photo of people in a workshop"></div>
<svg class="abs" style="left:404px;top:2796px" width="60" height="46" viewBox="0 0 60 46" fill="none" stroke="#fff" stroke-width="2.5" stroke-linecap="round"><path d="M4 42 C10 22 26 10 54 8"/><path d="M44 2 L54 8 L44 16"/></svg>
<h2 class="abs contact-h">CONTACT ME NOW</h2>
<p class="abs contact-p">Apsum cligula augue bibendum accumsan vestibulum ut commodo a mi &nbsp;Praesent elementum elit at tellus nec ultricies sit amet porttitor mattis enim in massa libero inte</p>
<div class="abs field" style="left:240px;width:276px">Your Name</div>
<div class="abs field" style="left:526px;width:274px">Email address</div>
<a class="abs btn subscribe" href="#">Subscribe</a>

<!-- Footer -->
<footer class="abs footer"></footer>
<nav class="abs foot-nav"><a href="#">HOME</a><a href="#">ABOUT</a><a href="#">BLOG</a><a href="#">VIDEO</a><a href="#">RESOURCES</a><a href="#">CONTACT</a></nav>
<div class="abs copy">© 2018 Company Name All right reserved</div>
<div class="abs social" aria-label="Social links"><span></span><span></span><span></span><span></span><span></span></div>

</body>
</html>
```